Animal Eye Clinic needs a Business card

We are a new veterinary ophthalmology practice (Ridgeline Pet Vision Care) and we need a business card designed. We only see animal eyes - we are not a regular veterinary clinic. We already have a logo. We are looking for a professional, good looking business card to hand out to our clients. We are looking for something simple but professional and contemporary. Our logo is likely the only picture/graphic that needs to be on the card.
Updates

Contact Information for Business Card

Delia Vossman, BSc, DVM, MSc, DipACVO
Veterinary Ophthalmologist

Phone: 250.418.3927
Email: ridgelinepetvisioncare@mailbox-example.net
Website: ridgelinepetvisioncare-example.net
Address: 1874 Thornbury Rd
Kelowna, BC, V1X 4M9

Colors

Designer to choose colors to be used in the design.

Requirements
Must have
• Our logo (attached)

```html
<!DOCTYPE html>
<html lang="en">
<head>
<meta charset="utf-8">
<title>Ridgeline Pet Vision Care — Business Card</title>
<link href="https://fonts.googleapis.com/css2?family=Roboto:wght@400;500&family=Roboto+Condensed:wght@700&display=swap" rel="stylesheet">
<style>
  :root {
    --stage: #3a3a3a;
    --card: #2b2b2b;
    --card-pattern: #303030;
    --faint-mark: #353535;
    --teal: #0f9cae;
    --ink: #f2f2f2;
    --ink-soft: #d9d9d9;
    --divider: #8a8a8a;
  }
  * { box-sizing: border-box; margin: 0; padding: 0; }
  html, body { width: 1200px; height: 901px; overflow: hidden; }
  body {
    background: var(--stage);
    font-family: "Roboto", Arial, sans-serif;
    position: relative;
  }
  .card {
    position: absolute;
    left: 250px;
    width: 700px;
    height: 400px;
    background: var(--card);
    box-shadow: 0 10px 30px rgba(0,0,0,.45);
    overflow: hidden;
  }
  .card--back { top: 30px; }
  .card--front { top: 470px; }

  .pattern {
    position: absolute; inset: 0;
    background: var(--card-pattern);
  }
  .brand {
    position: absolute;
    display: flex;
    align-items: center;
    gap: 10px;
    color: var(--teal);
    font-weight: 500;
    letter-spacing: .3px;
    white-space: nowrap;
  }
  .brand__dot {
    width: 30px; height: 30px; border-radius: 50%;
    background: var(--teal);
    flex: none;
  }
  .card--back .brand { right: 60px; top: 250px; font-size: 26px; }
  .card--back .brand__dot { width: 34px; height: 34px; }
  .card--front .brand { left: 30px; top: 122px; font-size: 19px; }

  .faint-mark {
    position: absolute;
    left: 60px; top: 30px;
    width: 340px; height: 300px;
    border-radius: 50%;
    background: radial-gradient(ellipse at center, var(--faint-mark) 0%, var(--card) 70%);
  }
  .divider {
    position: absolute;
    left: 325px; top: 95px;
    width: 1px; height: 150px;
    background: var(--divider);
  }
  .contact {
    position: absolute;
    left: 342px; right: 18px; top: 96px;
    color: var(--ink);
  }
  .contact__name {
    font-family: "Roboto Condensed", "Arial Narrow", sans-serif;
    font-weight: 700;
    font-size: 17px;
    color: var(--teal);
    text-transform: uppercase;
    white-space: nowrap;
  }
  .contact__title { font-size: 16px; margin: 2px 0 12px; color: var(--ink-soft); }
  .contact__list { list-style: none; }
  .contact__item {
    display: flex; align-items: center; gap: 8px;
    font-size: 13.5px; line-height: 22px; white-space: nowrap;
  }
  .contact__item svg { width: 12px; height: 12px; fill: var(--teal); flex: none; }
  .contact__accent { color: var(--teal); }
  .address {
    position: absolute;
    left: 0; right: 0; bottom: 34px;
    text-align: center;
    font-size: 16px;
    color: var(--ink);
  }
  .band {
    position: absolute;
    left: 0; right: 0; bottom: 0;
    height: 10px;
    background: var(--teal);
  }
</style>
</head>
<body>

<section class="card card--back">
  <div class="pattern" role="img" aria-label="Repeating tonal pattern of the practice's logo mark"></div>
  <div class="brand"><span class="brand__dot"></span>Ridgeline Pet Vision Care</div>
</section>

<section class="card card--front">
  <div class="faint-mark" role="img" aria-label="Large faint logo mark in the background"></div>
  <div class="brand"><span class="brand__dot"></span>Ridgeline Pet Vision Care</div>
  <div class="divider"></div>
  <div class="contact">
    <p class="contact__name">Delia Vossman, BSc, DVM, MSc, DipACVO</p>
    <p class="contact__title">Veterinary Ophthalmologist</p>
    <ul class="contact__list">
      <li class="contact__item">
        <svg viewBox="0 0 24 24" aria-hidden="true"><path d="M6.6 10.8a15 15 0 0 0 6.6 6.6l2.2-2.2a1 1 0 0 1 1-.25 11.4 11.4 0 0 0 3.6.57 1 1 0 0 1 1 1V20a1 1 0 0 1-1 1A17 17 0 0 1 3 4a1 1 0 0 1 1-1h3.5a1 1 0 0 1 1 1c0 1.25.2 2.45.57 3.570a1 1 0 0 1-.25 1z"/></svg>
        250.418.3927
      </li>
      <li class="contact__item">
        <svg viewBox="0 0 24 24" aria-hidden="true"><path d="M2 5h20v14H2zm2 2v.5l8 5 8-5V7l-8 5z"/></svg>
        ridgelinepetvisioncare@mailbox-example.net
      </li>
      <li class="contact__item">
        <svg viewBox="0 0 24 24" aria-hidden="true"><path d="M12 2a10 10 0 1 0 0 20 10 10 0 0 0 0-20zm0 2c1.5 2 2.4 4.6 2.6 7H9.4C9.6 8.6 10.5 6 12 4zM4.1 13h3.3c.1 2.3.8 4.4 1.9 6.2A8 8 0 0 1 4.1 13zm0-2a8 8 0 0 1 5.2-6.2C8.2 6.6 7.5 8.7 7.4 11zm5.3 2h5.2c-.2 2.4-1.1 4.8-2.6 7-1.5-2.2-2.4-4.600-2.6-7zm7.2 0h3.3a8 8 0 0 1-5.2 6.2c1.1-1.8 1.8-3.9 1.9-6.2zm0-2c-.1-2.3-.8-4.4-1.9-6.2A8 8 0 0 1 19.9 11z"/></svg>
        <span>www.<span class="contact__accent">ridgelinepetvisioncare-example</span>.net</span>
      </li>
    </ul>
  </div>
  <p class="address">1874 Thornbury Rd, Kelowna, BC, V1X 4M9</p>
  <div class="band"></div>
</section>

</body>
</html>
```